Renny Oskow - Free Personalised Health Consultation - "One size does not fit all"

This flyer will be left on tables/seats at speaking events and seminars and used to attain leads.

Top half will have "SMS me for a FREE Personalised Health Consultation" and my picture (see www.rennyoskow-demo.com and pick most engaging photo) and underneath my contact details. It must have lines with "Notes:" halfway down so people can take notes at the seminar and lines on the back with my contact details again and "Notes: with lines.

I am having a business card also being designed by Artvane for same and would like the flyer and business card to carry a similar feel/look for consistency.

Below is the brief for the business card being designed:
Business Card for www.rennyoskow-demo.com site. It is a trust site and I use it for 1:1 relatable connections. It is the one I use for building intimate 1:1 trust building and Exec Coaching Services and programs for high wealth individuals and corporates. I also have a commercial programmatic site of my personal health products and services and programs for main stream one to many. www.steadyforwardliving-demo.com that can also provoke thought for the www.rennyoskow-demo.com business card. (mind you will get a separate business card for that site, but want to provide context). It has a logo which you may want to draw from in designing the rennyoskow business card which is personal and is about building my brand. There is also a rennyoskow personal PX page and rennyoskow business PX page. I am a Certified Talent Compass 3.1 Coach with Norvik and you can get a corporate brief of me on there to give you more context https://www.norvikcoachhub-demo.com/coach/en-us/directory?search=renny

Target Market(s)

Exec, IT, Health conscious. Corporates wanting to run Health and Wellness programs. Those wanting to go from good to great. Millennials to Middleaged.

Industry/Entity Type

Health And Wellness

Font styles to use
Sans Serif
Other font styles liked:
• Arial and Calibri ok too

Colors

Designer to choose colors to be used in the design.

Requirements
Must have
• Picture of me - use best from www.rennyoskow-demo.com or can send one you choose.
• Contact details like my buisness card being designed by you guys in separate project.
• Name: Renny Oskow
• email: renny@rennyoskow-demo.,com
• Phone: Australia +61 400 000 137 Singapore: +65 9000 2468
Nice to have
• Open to ideas

```html
<!DOCTYPE html>
<html lang="en">
<head>
<meta charset="utf-8">
<title>Renny Oskow – Health Consultation Flyer</title>
<link href="https://fonts.googleapis.com/css2?family=Montserrat:wght@500;600;800&family=Arimo:wght@400&display=swap" rel="stylesheet">
<style>
  :root{
    --stage:#000000;
    --paper:#ffffff;
    --ink:#585858;
    --ink-dark:#1e1e1e;
    --swoosh-1:#e9e9ea;
    --swoosh-2:#dcdcdd;
    --rule:#bdbdbd;
    --band:#000000;
    --band-text:#ffffff;
    --strip:#e4e4e4;
  }
  html,body{margin:0;padding:0;overflow:hidden;background:var(--stage);}
  .canvas{position:relative;width:1200px;height:850px;background:var(--stage);overflow:hidden;}
  .page{position:absolute;top:64px;width:511px;height:722px;background:var(--paper);overflow:hidden;}
  .page--front{left:76px;}
  .page--back{left:614px;}
  .abs{position:absolute;}

  /* front */
  .front-swoosh{left:0;top:0;width:511px;height:460px;}
  .headline{left:31px;top:86px;margin:0;font-family:"Montserrat",sans-serif;font-weight:800;color:var(--ink);text-transform:uppercase;}
  .headline__lead{display:block;font-size:33px;line-height:40px;letter-spacing:0.2px;}
  .headline__line{display:block;font-size:21.5px;line-height:34px;letter-spacing:0.3px;}
  .portrait-front{left:229px;top:39px;width:255px;height:336px;border-radius:0 0 140px 140px / 0 0 120px 120px;
    background:linear-gradient(180deg,#8a8a8a 0%,#2a2a2a 45%,#3a3a3a 75%,#f2f2f2 100%);}
  .contact-list{left:34px;top:394px;margin:0;padding:0;list-style:none;font-family:"Montserrat",sans-serif;font-weight:500;font-size:9.6px;color:var(--ink-dark);letter-spacing:0.2px;}
  .contact-list li{position:relative;height:19.5px;padding-left:15px;line-height:16px;white-space:nowrap;}
  .contact-list svg{position:absolute;left:0;top:3px;width:10px;height:10px;}
  .signature-front{left:252px;top:434px;width:192px;height:30px;background:linear-gradient(90deg,#f1f1f1,#e6e6e6);border-radius:4px;}
  .notes-rules{left:0;top:0;width:511px;height:722px;}
  .script-deco{left:10px;top:636px;width:484px;height:64px;background:linear-gradient(90deg,rgba(0,0,0,0.03),rgba(0,0,0,0.05),rgba(0,0,0,0.03));border-radius:6px;}

  /* back */
  .back-art{left:0;top:0;width:511px;height:722px;}
  .portrait-back{left:0;top:498px;width:132px;height:156px;border-radius:60px 60px 0 0;
    background:linear-gradient(180deg,#b5b5b5 0%,#6f6f6f 50%,#8d8d8d 85%,#eeeeee 100%);}
  .contact-band{left:0;top:655px;width:372px;height:49px;}
  .band-text{font-family:"Arimo",sans-serif;font-size:9.4px;color:var(--band-text);letter-spacing:0;line-height:17px;}
  .band-phones{left:16px;top:663px;}
  .band-web{left:178px;top:663px;}
  .band-text .row{position:relative;padding-left:13px;white-space:nowrap;}
  .band-text svg{position:absolute;left:0;top:4px;width:9px;height:9px;}
  .band-divider{left:168px;top:666px;width:1px;height:30px;background:var(--band-text);}
  .signature-back{left:381px;top:662px;width:116px;height:21px;background:linear-gradient(90deg,#f1f1f1,#e6e6e6);border-radius:3px;}
</style>
</head>
<body>
<div class="canvas">

  <!-- FRONT -->
  <section class="page page--front">
    <svg class="abs front-swoosh" viewBox="0 0 511 460" aria-hidden="true">
      <path d="M0 0 H130 L470 180 A125 125 0 0 1 360 370 L0 270 Z" fill="var(--swoosh-1)"/>
      <path d="M40 0 H210 L440 130 L470 220 L60 60 Z" fill="var(--swoosh-2)" opacity="0.6"/>
      <circle cx="358" cy="241" r="125" fill="var(--swoosh-1)"/>
    </svg>

    <h1 class="abs headline">
      <span class="headline__lead">SMS me</span>
      <span class="headline__line">for a free</span>
      <span class="headline__line">personalised</span>
      <span class="headline__line">health</span>
      <span class="headline__line">consultation</span>
    </h1>

    <div class="abs portrait-front" role="img" aria-label="Black and white portrait of Renny Oskow smiling, arms crossed, in a dark t-shirt"></div>

    <ul class="abs contact-list">
      <li><svg viewBox="0 0 10 10"><path d="M2 0.5 L3.6 2.6 L2.7 3.6 Q3.8 6 6.4 7.3 L7.4 6.4 L9.5 8 L8.2 9.5 Q3 8.6 0.5 1.8 Z" fill="var(--ink-dark)"/></svg>AUSTRALIA: +61 400 000 137</li>
      <li>SINGAPORE: +65 9000 2468</li>
      <li><svg viewBox="0 0 10 10"><rect x="0.5" y="1.8" width="9" height="6.4" fill="var(--ink-dark)"/><path d="M0.8 2.2 L5 5.4 L9.2 2.2" stroke="#fff" stroke-width="0.8" fill="none"/></svg>RENNY@RENNYOSKOW-DEMO.COM</li>
      <li><svg viewBox="0 0 10 10"><circle cx="5" cy="5" r="4.5" fill="var(--ink-dark)"/><path d="M0.5 5 H9.5 M5 0.5 V9.5 M2 2.5 Q5 4 8 2.5 M2 7.5 Q5 6 8 7.5" stroke="#fff" stroke-width="0.6" fill="none"/></svg>WWW.RENNYOSKOW-DEMO.COM</li>
    </ul>

    <div class="abs signature-front" role="img" aria-label="Handwritten signature: Renny Oskow"></div>

    <div class="abs script-deco" role="img" aria-label="Faint oversized handwritten name Renny Oskow behind the note lines"></div>

    <svg class="abs notes-rules" viewBox="0 0 511 722" aria-hidden="true">
      <g stroke="var(--rule)" stroke-width="0.8">
        <line x1="19" y1="503" x2="491" y2="503"/>
        <line x1="19" y1="531.6" x2="491" y2="531.6"/>
        <line x1="19" y1="560.2" x2="491" y2="560.2"/>
        <line x1="19" y1="588.8" x2="491" y2="588.8"/>
        <line x1="19" y1="617.4" x2="491" y2="617.4"/>
        <line x1="19" y1="646" x2="491" y2="646"/>
        <line x1="19" y1="674.6" x2="491" y2="674.6"/>
        <line x1="19" y1="703.2" x2="491" y2="703.2"/>
      </g>
    </svg>
  </section>

  <!-- BACK -->
  <section class="page page--back">
    <svg class="abs back-art" viewBox="0 0 511 722" aria-hidden="true">
      <circle cx="450" cy="709" r="77" fill="var(--swoosh-1)"/>
      <rect x="0" y="704" width="511" height="18" fill="var(--strip)"/>
      <g stroke="var(--rule)" stroke-width="0.8">
        <line x1="21" y1="34" x2="491" y2="34"/>
        <line x1="21" y1="62.6" x2="491" y2="62.6"/>
        <line x1="21" y1="91.2" x2="491" y2="91.2"/>
        <line x1="21" y1="119.8" x2="491" y2="119.8"/>
        <line x1="21" y1="148.4" x2="491" y2="148.4"/>
        <line x1="21" y1="177" x2="491" y2="177"/>
        <line x1="21" y1="205.6" x2="491" y2="205.6"/>
        <line x1="21" y1="234.2" x2="491" y2="234.2"/>
        <line x1="21" y1="262.8" x2="491" y2="262.8"/>
        <line x1="21" y1="291.4" x2="491" y2="291.4"/>
        <line x1="21" y1="320" x2="491" y2="320"/>
        <line x1="21" y1="348.6" x2="491" y2="348.6"/>
        <line x1="21" y1="377.2" x2="491" y2="377.2"/>
        <line x1="21" y1="405.8" x2="491" y2="405.8"/>
        <line x1="21" y1="434.4" x2="491" y2="434.4"/>
        <line x1="21" y1="463" x2="491" y2="463"/>
        <line x1="21" y1="491.6" x2="491" y2="491.6"/>
        <line x1="141" y1="520.2" x2="491" y2="520.2"/>
        <line x1="141" y1="548.8" x2="491" y2="548.8"/>
        <line x1="141" y1="577.4" x2="491" y2="577.4"/>
        <line x1="141" y1="606" x2="491" y2="606"/>
        <line x1="141" y1="634.6" x2="491" y2="634.6"/>
        <line x1="390" y1="687" x2="511" y2="687"/>
      </g>
    </svg>

    <div class="abs portrait-back" role="img" aria-label="Faded black and white portrait of Renny Oskow smiling"></div>

    <svg class="abs contact-band" viewBox="0 0 372 49" aria-hidden="true">
      <polygon points="0,0 372,0 357,49 0,49" fill="var(--band)"/>
    </svg>

    <div class="abs band-text band-phones">
      <div class="row"><svg viewBox="0 0 10 10"><path d="M2 0.5 L3.6 2.6 L2.7 3.6 Q3.8 6 6.4 7.3 L7.4 6.4 L9.5 8 L8.2 9.5 Q3 8.6 0.5 1.8 Z" fill="#fff"/></svg>AUSTRALIA:&nbsp; +61 400 000 137</div>
      <div class="row">SINGAPORE: +65 9000 2468</div>
    </div>
    <div class="abs band-divider"></div>
    <div class="abs band-text band-web">
      <div class="row"><svg viewBox="0 0 10 10"><rect x="0.5" y="1.8" width="9" height="6.4" fill="#fff"/><path d="M0.8 2.2 L5 5.4 L9.2 2.2" stroke="#000" stroke-width="0.8" fill="none"/></svg>RENNY@RENNYOSKOW-DEMO.COM</div>
      <div class="row"><svg viewBox="0 0 10 10"><circle cx="5" cy="5" r="4.5" fill="#fff"/><path d="M0.5 5 H9.5 M5 0.5 V9.5 M2 2.5 Q5 4 8 2.5 M2 7.5 Q5 6 8 7.5" stroke="#000" stroke-width="0.6" fill="none"/></svg>WWW.RENNYOSKOW-DEMO.COM</div>
    </div>

    <div class="abs signature-back" role="img" aria-label="Handwritten signature: Renny Oskow"></div>
  </section>

</div>
</body>
</html>
```